Industrial Bolting Tool Safety Ad

We need an ad designed. Ad size is 4" x 4.75". Our company is VornelTek. We build large industrial bolting tools that are designed for use with very large bolts in large wind turbines (wind towers). If these large tools aren't equipped with some sort of safety measures, significant hand and wrist injuries can occur, such as crushed and mutilated fingers and hands. What makes our tools unique is that they are dual-levered (two handled), which means they require two hands to start, making accidental start highly unlikely. Safety is the thing we want to stress. Our tools help protect the most valuable asset - the tool operator. An image of a worker with a finger injury is attached to use for the background<br/>- VornelTek QX Company logo should be used (attached)<br/>- Ad headline should be: Safety is Vital in Critical Bolting<br/>- Ad subhead should be: <br/>High Torque Dual-Lever DC Nutrunners<br/>Designed with Safety in Mind<br/><br/>Apart from the safety aspect, here are some additional things to know. Our tool operates with a controller (a picture of the basic controller/tool setup is included with the design images). There is constant communication happening between the controller and the tool so that the bolts are tightened accurately every time. The controller works with many tools. An image of each model of tool is attached. Please include each image in the ad, although only one needs to be connected to the controller (the original image of the controller already has this so the other models can just stand free as-is).

Target Market(s)

Wind Turbine Manufacturers and Turbine Maintenance Engineers

Font styles to use
Sans Serif

Colors
9bcb3c
add136
cadf82

Requirements
Must have
• VornelTek QX Company Logo
• Headline: Safety is Vital in Critical Bolting
• Subhead: High-Torque Dual-Lever Nutrunners
• Designed with Safety in Mind

```html
<!DOCTYPE html>
<html lang="en">
<head>
<meta charset="utf-8">
<title>VornelTek QX – Safety is Vital in Critical Bolting</title>
<link rel="stylesheet" href="https://fonts.googleapis.com/css2?family=Anton&family=Titillium+Web:ital,wght@0,600;0,700;1,600&display=swap">
<style>
  :root {
    --page: #e9e9e9;
    --ink: #231f20;
    --white: #ffffff;
    --yellow: #f2c200;
    --sky: #6d97c6;
    --sky-light: #9dbbd9;
    --vest: #f2661a;
    --skin: #d8a084;
    --skin-deep: #b97a62;
    --helmet: #1f9a4a;
    --teal: #2a7d78;
    --steel: #8a8a8a;
  }
  * { margin: 0; padding: 0; box-sizing: border-box; }
  html, body { width: 1200px; height: 1200px; overflow: hidden; background: var(--page); }
  .ad {
    position: absolute; left: 128px; top: 40px;
    width: 944px; height: 1120px;
    background: var(--ink);
    overflow: hidden;
    font-family: "Titillium Web", sans-serif;
    color: var(--white);
  }
  .ad-hero { position: absolute; left: 0; top: 0; width: 944px; height: 620px; }
  .headline {
    position: absolute; left: 0; top: 0; width: 100%;
    text-align: center;
    font-family: "Anton", sans-serif;
    font-weight: 400;
    text-transform: uppercase;
    color: var(--white);
    line-height: 1;
    text-shadow:
      -2px -2px 0 var(--ink), 2px -2px 0 var(--ink), -2px 2px 0 var(--ink), 2px 2px 0 var(--ink),
      0 -2.5px 0 var(--ink), 0 2.5px 0 var(--ink), -2.5px 0 0 var(--ink), 2.5px 0 0 var(--ink);
  }
  .headline-line {
    position: absolute; left: 50%; white-space: nowrap;
    transform-origin: center top;
  }
  .headline-line1 { top: 38px; font-size: 96px; transform: translateX(-50%) scaleX(1.12); }
  .headline-line2 { top: 138px; font-size: 110px; transform: translateX(-50%) scaleX(1.19); }
  .subhead {
    position: absolute; top: 606px; width: 100%;
    text-align: center; font-weight: 600; font-size: 33px; letter-spacing: 0.5px;
  }
  .tagline {
    position: absolute; left: 186px; top: 661px; width: 562px; height: 48px;
    border-radius: 24px; background: var(--yellow); color: var(--ink);
    text-align: center; font-weight: 700; font-size: 30px; line-height: 48px; letter-spacing: 1px;
  }
  .product-row { position: absolute; left: 0; top: 748px; width: 944px; height: 250px; }
  .product { position: absolute; top: 0; width: 220px; text-align: center; }
  .product-image {
    display: block; margin: 0 auto; width: 176px; height: 176px; border-radius: 50%;
    border: 7px solid var(--yellow);
    background: #f4f4f4;
  }
  .product-image--upright {
    background:
      radial-gradient(ellipse 22% 42% at 50% 52%, #5e5a55 0%, #8c8780 55%, rgba(140,135,128,0) 100%),
      radial-gradient(ellipse 38% 14% at 50% 20%, #2d2f33 0%, rgba(45,47,51,0) 100%),
      radial-gradient(circle at 50% 50%, #ffffff 55%, #e2e2e2 100%);
  }
  .product-image--pistol {
    background:
      radial-gradient(ellipse 44% 14% at 50% 40%, #9a9894 0%, #6d6b68 60%, rgba(109,107,104,0) 100%),
      radial-gradient(ellipse 10% 26% at 34% 62%, #2b2b2d 0%, rgba(43,43,45,0) 100%),
      radial-gradient(circle at 50% 50%, #ffffff 55%, #e2e2e2 100%);
  }
  .product-image--angled {
    background:
      radial-gradient(ellipse 42% 16% at 54% 48%, #8f8d89 0%, #5b5a58 60%, rgba(91,90,88,0) 100%),
      radial-gradient(ellipse 14% 12% at 30% 66%, #2e2e30 0%, rgba(46,46,48,0) 100%),
      radial-gradient(circle at 50% 50%, #ffffff 55%, #e2e2e2 100%);
  }
  .product-image--kit {
    background:
      radial-gradient(ellipse 32% 30% at 38% 55%, #6b6c6e 0%, #3a3b3d 60%, rgba(58,59,61,0) 100%),
      radial-gradient(ellipse 10% 22% at 74% 42%, #3a3a3c 0%, rgba(58,58,60,0) 100%),
      radial-gradient(ellipse 6% 4% at 48% 60%, #d9452a 0%, rgba(217,69,42,0) 100%),
      radial-gradient(circle at 50% 50%, #ffffff 55%, #e2e2e2 100%);
  }
  .product-label { margin-top: 14px; font-style: italic; font-weight: 600; font-size: 18px; line-height: 1.25; }
  .divider {
    position: absolute; top: 2px; height: 218px; width: 0;
    border-left: 3px dotted #cfcfcf;
  }
  .brand {
    position: absolute; top: 1018px; width: 100%;
    display: flex; justify-content: center; align-items: center; gap: 14px;
  }
  .brand-mark { width: 40px; height: 40px; border-radius: 50%; background: var(--white); }
  .brand-name { font-weight: 700; font-size: 40px; color: var(--white); letter-spacing: 0.5px; }
</style>
</head>
<body>
<main class="ad">
  <svg class="ad-hero" viewBox="0 0 944 620">
    <defs>
      <clipPath id="heroClip">
        <path d="M0 0 H944 V345 C760 480 520 590 260 588 C150 586 60 575 0 560 Z"/>
      </clipPath>
      <linearGradient id="skyTone" x1="0" y1="0" x2="0" y2="1">
        <stop offset="0" stop-color="var(--sky)"/>
        <stop offset="1" stop-color="var(--sky-light)"/>
      </linearGradient>
      <radialGradient id="helmetTone" cx="0.5" cy="0.5" r="0.5">
        <stop offset="0" stop-color="var(--helmet)"/>
        <stop offset="1" stop-color="var(--helmet)" stop-opacity="0"/>
      </radialGradient>
      <radialGradient id="vestTone" cx="0.5" cy="0.5" r="0.5">
        <stop offset="0" stop-color="var(--vest)"/>
        <stop offset="0.6" stop-color="var(--vest)" stop-opacity="0.85"/>
        <stop offset="1" stop-color="var(--vest)" stop-opacity="0"/>
      </radialGradient>
      <radialGradient id="skinTone" cx="0.5" cy="0.5" r="0.5">
        <stop offset="0" stop-color="var(--skin)"/>
        <stop offset="0.7" stop-color="var(--skin-deep)" stop-opacity="0.8"/>
        <stop offset="1" stop-color="var(--skin-deep)" stop-opacity="0"/>
      </radialGradient>
      <radialGradient id="tealTone" cx="0.5" cy="0.5" r="0.5">
        <stop offset="0" stop-color="var(--teal)"/>
        <stop offset="1" stop-color="var(--teal)" stop-opacity="0"/>
      </radialGradient>
    </defs>
    <path class="swoosh-yellow" fill="var(--yellow)" d="M0 0 H944 V410 C790 520 580 602 330 598 C200 596 90 585 0 566 Z"/>
    <path class="swoosh-white" fill="var(--white)" d="M0 0 H944 V380 C770 505 530 598 300 594 C180 592 80 580 0 565 Z"/>
    <g class="hero-photo" role="img" aria-label="Photo: wind turbine worker in green hard hat and orange hi-vis jacket pressing a bloodied cloth to an injured finger" clip-path="url(#heroClip)">
      <rect width="944" height="620" fill="url(#skyTone)"/>
      <ellipse cx="90" cy="300" rx="150" ry="200" fill="url(#tealTone)"/>
      <ellipse cx="690" cy="20" rx="240" ry="90" fill="url(#helmetTone)"/>
      <ellipse cx="830" cy="330" rx="260" ry="280" fill="url(#vestTone)"/>
      <ellipse cx="560" cy="430" rx="220" ry="200" fill="url(#vestTone)" opacity="0.7"/>
      <ellipse cx="660" cy="250" rx="170" ry="210" fill="url(#skinTone)" opacity="0.75"/>
      <ellipse cx="330" cy="520" rx="380" ry="210" fill="url(#skinTone)"/>
    </g>
  </svg>

  <h1 class="headline">
    <span class="headline-line headline-line1">Safety is Vital in</span>
    <span class="headline-line headline-line2">Critical Bolting</span>
  </h1>

  <p class="subhead">HIGH TORQUE DUAL-LEVER DC NUTRUNNERS</p>
  <p class="tagline">DESIGNED WITH SAFETY IN MIND</p>

  <section class="product-row">
    <div class="product" style="left:28px">
      <span class="product-image product-image--upright" role="img" aria-label="17,000 Nm dual-lever nutrunner tool"></span>
      <p class="product-label">17,000 Nm Tool</p>
    </div>
    <span class="divider" style="left:249px"></span>
    <div class="product" style="left:252px">
      <span class="product-image product-image--pistol" role="img" aria-label="Nutrunner with KRP pistol handle"></span>
      <p class="product-label">KRP Handle</p>
    </div>
    <span class="divider" style="left:475px"></span>
    <div class="product" style="left:476px">
      <span class="product-image product-image--angled" role="img" aria-label="Nutrunner with KRS handle"></span>
      <p class="product-label">KRS Handle</p>
    </div>
    <span class="divider" style="left:694px"></span>
    <div class="product" style="left:698px">
      <span class="product-image product-image--kit" role="img" aria-label="Controller in carry case connected to J-handled dual-lever tool"></span>
      <p class="product-label">VQC4WF with J-Handled<br>Dual-Lever Tool</p>
    </div>
  </section>

  <div class="brand">
    <span class="brand-mark"></span>
    <span class="brand-name">VornelTek QX</span>
  </div>
</main>
</body>
</html>
```